Belmont Ridge Business Card Design Project

We have recently rebranded and would like to design new business cards that incorporate the corporate logo - double sided cards with corporate logo on one side and contact details on the other

Target Market(s)

Sophisticated and high net worth investors and finance industry professionals

Industry/Entity Type

Funds Management

Contact Information for Business Card

The card should prominently feature the company name and logo. Other details will be standard contact details for each staff member - name, address, phone, email, website

Colors
0054AA
0677BA
7BADD7
CADEEF
E8F1F8

Requirements
Must have
• Double-sided design with one side prominently featuring the corporate logo and the other side with all standard contact details

```html
<!DOCTYPE html>
<html lang="en">
<head>
<meta charset="utf-8">
<title>Belmont Ridge Business Card</title>
<link href="https://fonts.googleapis.com/css2?family=Arimo:wght@400;700&display=swap" rel="stylesheet">
<style>
  :root {
    --navy: #1f4577;
    --navy-deep: #173a68;
    --accent: #0054AA;
    --sky: #7BADD7;
    --mist: #CADEEF;
    --white: #ffffff;
    --backdrop: #e6e6e6;
  }
  * { box-sizing: border-box; margin: 0; padding: 0; }
  html, body { width: 1200px; height: 802px; overflow: hidden; }
  body {
    background: var(--backdrop);
    font-family: "Arimo", Arial, sans-serif;
    display: flex;
    align-items: center;
    justify-content: center;
    gap: 60px;
  }
  .card {
    position: relative;
    width: 530px;
    height: 303px;
    background: var(--navy);
    color: var(--white);
    overflow: hidden;
    box-shadow: 0 4px 14px rgba(0,0,0,0.18);
  }
  /* Front */
  .holder { position: absolute; top: 34px; right: 36px; text-align: right; }
  .holder-name { font-weight: 700; font-size: 17px; letter-spacing: 0.5px; }
  .holder-role { font-size: 11px; margin-top: 3px; }
  .brand {
    position: absolute; left: 36px; top: 112px;
    display: flex; align-items: center; gap: 10px;
  }
  .brand-dot { width: 14px; height: 14px; border-radius: 50%; background: var(--white); flex: none; }
  .brand-name { font-size: 26px; font-weight: 700; letter-spacing: 1px; text-transform: uppercase; white-space: nowrap; }
  .brand-art {
    position: absolute; right: 30px; top: 96px;
    width: 160px; height: 150px;
    background: linear-gradient(135deg, rgba(255,255,255,0.9), rgba(202,222,239,0.6));
    border-radius: 4px;
  }
  .contacts {
    position: absolute; left: 36px; top: 190px;
    list-style: none; font-size: 13px; line-height: 1.55;
  }
  .contacts li { display: flex; align-items: center; gap: 8px; white-space: nowrap; }
  .contacts svg { width: 12px; height: 12px; fill: var(--white); flex: none; }
  .address-band {
    position: absolute; left: 0; right: 0; bottom: 0; height: 34px;
    background: var(--white); color: var(--navy);
    font-size: 13px; display: flex; align-items: center; padding-left: 36px;
    white-space: nowrap;
  }
  /* Back */
  .pattern {
    position: absolute; inset: 0;
    background: linear-gradient(120deg, var(--navy-deep) 0%, var(--navy) 45%, #3f74b6 100%);
  }
  .back-brand {
    position: absolute; inset: 0;
    display: flex; align-items: center; justify-content: center; gap: 10px;
  }
</style>
</head>
<body>
  <section class="card card-front">
    <div class="holder">
      <p class="holder-name">DANIEL HARTLEY</p>
      <p class="holder-role">Manager</p>
    </div>
    <div class="brand">
      <span class="brand-dot"></span>
      <span class="brand-name">Belmont Ridge</span>
    </div>
    <div class="brand-art" role="img" aria-label="Large brand decoration in white"></div>
    <ul class="contacts">
      <li><svg viewBox="0 0 24 24"><path d="M6.6 10.8a15 15 0 0 0 6.6 6.6l2.2-2.2a1 1 0 0 1 1-.25 11.4 11.4 0 0 0 3.6.57 1 1 0 0 1 1 1V20a1 1 0 0 1-1 1A17 17 0 0 1 3 4a1 1 0 0 1 1-1h3.5a1 1 0 0 1 1 1c0 1.25.2 2.45.57 3.57a1 1 0 0 1-.25 1z"/></svg>555-014-7320</li>
      <li><svg viewBox="0 0 24 24"><path d="M2 5h20v14H2z M4 7v1l8 5 8-5V7l-8 5z" fill-rule="evenodd"/></svg>dhartley@belmontridge.com</li>
      <li><svg viewBox="0 0 24 24"><path d="M12 2a10 10 0 1 0 0 20 10 10 0 0 0 0-20zm0 2c1 0 2.3 2.2 2.7 5H9.3C9.7 6.2 11 4 12 4zm-3 7h6v2H9zm.3 4h5.4c-.4 2.8-1.7 5-2.7 5s-2.3-2.2-2.7-5z"/></svg>www.belmontridge.com</li>
    </ul>
    <div class="address-band">48 Harbour Lane, Fairview, NY 10021</div>
  </section>

  <section class="card card-back">
    <div class="pattern" role="img" aria-label="Embossed repeating brand pattern in blue tones"></div>
    <div class="back-brand">
      <span class="brand-dot"></span>
      <span class="brand-name">Belmont Ridge</span>
    </div>
  </section>
</body>
</html>
```